Business Card for Lantern Reach

Please design a Modern Business card for a Online Marketing Company

Website: http://www.lanternreach-example.com.au

Please do NOT include physical address in design.

```html
<!DOCTYPE html>
<html lang="en">
<head>
<meta charset="utf-8">
<title>Lantern Reach – Business Card</title>
<link href="https://fonts.googleapis.com/css2?family=Open+Sans:wght@400;600;700&display=swap" rel="stylesheet">
<style>
  :root {
    --stage: #5a3a22;
    --card-white: #ffffff;
    --panel-grey: #eef0f1;
    --brand-orange: #ff4a0a;
    --ink: #222222;
    --ink-soft: #555555;
    --on-orange: #ffffff;
  }
  * { box-sizing: border-box; margin: 0; padding: 0; }
  html, body { width: 1200px; height: 466px; overflow: hidden; }
  body {
    background: var(--stage);
    position: relative;
    font-family: "Open Sans", Arial, sans-serif;
  }
  .card {
    position: absolute;
    top: 83px;
    width: 520px;
    height: 300px;
    border-radius: 26px;
    overflow: hidden;
  }
  /* Front side */
  .card-front {
    left: 40px;
    background: var(--card-white);
    display: flex;
  }
  .front-brand {
    width: 230px;
    display: flex;
    flex-direction: column;
    justify-content: center;
    align-items: center;
    padding-top: 60px;
  }
  .front-brand .brand-name {
    font-weight: 600;
    font-size: 22px;
    color: var(--ink);
  }
  .front-brand .tagline {
    font-weight: 400;
    font-size: 12px;
    color: var(--ink-soft);
    margin-top: 2px;
  }
  .front-details {
    flex: 1;
    background: var(--panel-grey);
    border-radius: 34px 0 0 34px;
    padding: 90px 20px 0 26px;
  }
  .person-name {
    font-weight: 700;
    font-size: 18px;
    color: var(--ink);
    line-height: 1.1;
  }
  .person-title {
    font-size: 13px;
    color: var(--ink-soft);
  }
  .contact-list { list-style: none; margin-top: 42px; }
  .contact-list li {
    display: flex;
    align-items: center;
    gap: 7px;
    font-size: 12px;
    color: var(--ink);
    line-height: 1.55;
  }
  .contact-list svg { width: 11px; height: 11px; flex: none; }
  /* Back side */
  .card-back {
    left: 640px;
    background: var(--brand-orange);
    color: var(--on-orange);
    text-align: center;
  }
  .card-back .brand-name {
    position: absolute;
    top: 98px; left: 0; right: 0;
    font-weight: 600;
    font-size: 38px;
  }
  .card-back .tagline {
    position: absolute;
    top: 152px; left: 0; right: 0;
    font-weight: 400;
    font-size: 18px;
  }
  .card-back .web {
    position: absolute;
    bottom: 40px; left: 0; right: 0;
    font-size: 17px;
    letter-spacing: 0.6px;
  }
</style>
</head>
<body>
  <section class="card card-front" aria-label="Card front">
    <div class="front-brand">
      <p class="brand-name">Lantern Reach</p>
      <p class="tagline">Be found online - Grow online</p>
    </div>
    <div class="front-details">
      <p class="person-name">Your Name</p>
      <p class="person-title">Title</p>
      <ul class="contact-list">
        <li>
          <svg viewBox="0 0 12 12" aria-hidden="true"><path d="M3 1 L5 3.5 L4 5 Q5 7 7 8 L8.5 7 L11 9 L9.5 11 Q4 10.5 1 3 Z" fill="var(--ink)"/></svg>
          0400 123 456
        </li>
        <li>
          <svg viewBox="0 0 12 12" aria-hidden="true"><rect x="0.5" y="2.5" width="11" height="7.5" fill="var(--ink)"/><path d="M0.5 2.5 L6 7 L11.5 2.5" stroke="#fff" fill="none" stroke-width="1"/></svg>
          plan@lanternreach-example.com.au
        </li>
        <li>
          <svg viewBox="0 0 12 12" aria-hidden="true"><circle cx="6" cy="6" r="5" fill="none" stroke="var(--ink)" stroke-width="1.2"/><ellipse cx="6" cy="6" rx="2.2" ry="5" fill="none" stroke="var(--ink)" stroke-width="1"/><line x1="1" y1="6" x2="11" y2="6" stroke="var(--ink)" stroke-width="1"/></svg>
          www.lanternreach-example.com.au
        </li>
      </ul>
    </div>
  </section>

  <section class="card card-back" aria-label="Card back">
    <p class="brand-name">Lantern Reach</p>
    <p class="tagline">Be found online - Grow online</p>
    <p class="web">www.lanternreach-example.com.au</p>
  </section>
</body>
</html>
```